Corportate Power Point Template

We need a corporate PPT Design for our startup Big Data company.

Basically, our company will ingest, analyze and generate dynamic Dashboards with data consumed from different sources like Social Networks, Enterprise Legacy Systems such as e-Commerce, ERP, CRM and others.

Company is headquartered in Brazil, but will have a global presence.

Industry/Entity Type

It Company

```html
<!DOCTYPE html>
<html lang="en">
<head>
<meta charset="utf-8">
<title>Nexora Labs – Corporate Presentation Template</title>
<link rel="stylesheet" href="https://fonts.googleapis.com/css2?family=Roboto+Condensed:wght@400;700&family=Open+Sans:wght@400;600;700&display=swap">
<style>
  :root{
    --orange:#f26b21;
    --orange-mid:#f5874a;
    --orange-light:#f8a877;
    --orange-pale:#fde4d1;
    --amber:#f7b55a;
    --ink:#3a3a3a;
    --grey:#6b6b6b;
    --grey-mid:#9a9a9a;
    --grey-light:#d6d6d6;
    --line:#ececec;
    --stage:#000;
    --paper:#fff;
  }
  *{box-sizing:border-box;margin:0;padding:0}
  html,body{width:1200px;height:916px;overflow:hidden;background:var(--stage)}
  body{font-family:"Open Sans",Arial,sans-serif;color:var(--ink)}
  .deck{display:grid;grid-template-columns:repeat(4,287px);grid-template-rows:repeat(4,215px);gap:12px;padding:8px}
  .slide{position:relative;width:287px;height:215px;overflow:hidden;
    background:radial-gradient(circle at 92% 6%,var(--orange-pale) 0,rgba(253,228,209,0) 38%),var(--paper)}
  .slide.warm{background:linear-gradient(135deg,#fcd9bd 0%,#fdeadb 35%,#fff7f1 60%,#fff 78%,#fdeee2 100%)}

  /* header */
  .title{position:absolute;left:0;top:9px;height:16px;padding-left:9px;border-left:3px solid var(--orange);
    font-family:"Roboto Condensed",Arial,sans-serif;font-size:14px;line-height:16px;color:var(--ink)}
  .title b{font-weight:400;color:var(--orange)}

  /* footer */
  .footer{position:absolute;left:0;right:0;bottom:0;height:18px;border-top:1px solid var(--line);
    display:flex;align-items:center;justify-content:space-between;padding:0 4px;font-size:4.6px;color:var(--ink)}
  .footer .who em{font-style:normal;color:var(--orange)}
  .footer.ruled{border-top:1px solid var(--orange);height:14px}
  .footer .page{color:var(--orange)}

  .brand{display:inline-flex;align-items:center;gap:3px;font-family:"Roboto Condensed",Arial,sans-serif;
    font-weight:400;color:var(--orange);font-size:11px;line-height:1;white-space:nowrap}
  .brand i{display:inline-block;width:7px;height:7px;background:var(--grey)}
  .brand.lg{font-size:21px;gap:6px}
  .brand.lg i{width:13px;height:13px}

  .photo{position:absolute;background:linear-gradient(160deg,#e9e6e6 0%,#c9c4c6 45%,#f1efef 70%,#b9b3b8 100%)}
  .photo.lilac{background:linear-gradient(150deg,#e8d8df 0%,#c9b5c6 40%,#efe6ea 70%,#b49fb8 100%)}

  .txt{font-size:4.4px;line-height:6.2px;color:var(--grey)}
  .just{text-align:justify}

  /* cover */
  .cover{position:absolute;left:0;right:0;top:88px;text-align:center}
  .cover h1{font-family:"Roboto Condensed",Arial,sans-serif;font-weight:400;font-size:13px;margin-top:12px;color:var(--ink)}
  .cover h1 b{font-weight:400;color:var(--orange)}
  .cover .sub{font-size:4.6px;line-height:8px;color:var(--ink);margin-top:3px}
  .cover .presenter{font-size:4.8px;color:var(--ink);margin-top:6px}
  .cover .presenter em{display:block;font-style:normal;color:var(--orange);font-size:6px;margin-top:2px}
  .cover.right{left:auto;right:10px;text-align:right;top:92px}

  /* index */
  .index{position:absolute;left:16px;top:50px;display:grid;grid-template-columns:130px 130px;column-gap:10px;row-gap:10px}
  .index li{list-style:none;display:flex;align-items:center;height:17px;background:linear-gradient(90deg,#f6f6f6,#fff);font-size:5.5px;color:var(--ink)}
  .index .num{width:17px;height:17px;background:var(--grey);color:#fff;font-family:"Roboto Condensed",Arial,sans-serif;font-size:9px;display:flex;align-items:center;justify-content:center;margin-right:8px;border:2px solid #efefef}

  /* bullets */
  .bullets{position:absolute;left:10px;top:41px}
  .bullets li{list-style:none;display:flex;align-items:center;height:18px;font-size:5.2px;font-weight:600;color:var(--ink)}
  .bullets svg{margin-right:7px}

  /* two-column text */
  .cols{position:absolute;display:grid;grid-template-columns:1fr 1fr;column-gap:12px}
  .cols h3{font-size:6.4px;font-weight:600;color:var(--orange);margin-bottom:8px}
  .cols p{margin-bottom:8px}

  /* table */
  .table{position:absolute;left:21px;top:75px;width:257px;border:3px solid #f0f0f0;border-collapse:collapse;font-size:4.4px}
  .table th{background:var(--orange);color:#fff;font-weight:600;text-align:left;padding:4px 6px;height:14px}
  .table td{padding:0 6px;height:18px;color:var(--ink);border-top:2px solid #fff}
  .table tr:nth-child(odd) td{background:#ececec}
  .table tr:nth-child(even) td{background:#f6f6f6}

  /* three cards */
  .cards{position:absolute;left:13px;top:40px;display:grid;grid-template-columns:repeat(3,77px);column-gap:15px}
  .cards .ph{height:58px;background:#e6e6e6;display:flex;align-items:center;justify-content:center;font-size:4px;color:#bdbdbd}
  .cards .lbl{background:var(--orange);color:#fff;font-size:5.6px;padding:2px 3px;margin:6px 0 3px}
  .cards .txt p{margin-bottom:6px}

  /* director */
  .portrait{position:absolute;left:13px;top:46px;width:84px;height:118px;border:1px solid #e4e4e4;background:#fff;box-shadow:0 1px 2px rgba(0,0,0,.08);
    display:flex;align-items:flex-start;justify-content:center;padding-top:50px;font-size:4.2px;color:var(--orange-light)}
  .nameband{position:absolute;left:13px;top:154px;width:84px;height:12px;background:var(--orange);color:#fff;font-size:6.4px;padding:1px 4px}
  .role{position:absolute;left:15px;top:168px;font-size:5.6px;color:var(--ink)}
  .bio{position:absolute;left:107px;top:47px;width:172px}
  .bio p{margin-bottom:5px}
  .bio .contact{color:var(--orange)}

  /* pie */
  .lead{font-size:7px;font-weight:600;color:var(--orange)}

  /* agenda */
  .agenda-h{position:absolute;left:12px;top:36px;font-family:"Roboto Condensed",Arial,sans-serif;font-size:10px;font-weight:700;color:var(--orange)}
  .agenda{position:absolute;left:12px;top:52px}
  .agenda .row{position:relative;height:32px;display:flex;align-items:flex-start}
  .agenda .chev{width:40px;height:30px;position:relative}
  .agenda .chev span{position:absolute;left:0;right:0;top:10px;text-align:center;color:#fff;font-size:5px;font-weight:700}
  .agenda .box{margin-left:0;width:245px;height:22px;border:1px solid #f2b38e;border-left:none;margin-top:4px;padding:2px 0 0 2px;font-size:4.8px;line-height:8px;color:var(--ink);width:219px}

  /* closing */
  .closing-brand{position:absolute;left:22px;top:108px}
  .closing-presenter{position:absolute;left:28px;top:132px;font-size:5.2px;color:var(--ink)}
  .closing-presenter em{font-style:normal;color:var(--orange)}
  .contact-card{position:absolute;left:155px;top:84px;width:125px}
  .contact-card h2{font-family:"Roboto Condensed",Arial,sans-serif;font-weight:400;font-size:10px;color:var(--orange)}
  .contact-card .txt{color:var(--ink);margin:2px 0 8px}
  .contact-card li{list-style:none;display:flex;align-items:center;gap:5px;font-size:4.8px;color:var(--ink);height:15px}
  .contact-card li i{width:7px;height:7px;border-radius:50%;background:var(--orange);display:inline-block}
</style>
</head>
<body>
<main class="deck">

  <!-- 1 cover centered -->
  <section class="slide warm">
    <div class="cover">
      <span class="brand lg"><i></i>Nexora Labs</span>
      <h1><b>Project</b> Title Here</h1>
      <p class="sub">Subtext here Subtext here Subtext here Subtext here<br>Subtext here Subtext here Subtext here</p>
      <p class="presenter">Persentatator Name<em>Marco Teixeira</em></p>
    </div>
    <footer class="footer ruled"><span>Copyright text here</span><span class="page">Page 01</span></footer>
  </section>

  <!-- 2 cover right -->
  <section class="slide warm">
    <div class="cover right">
      <span class="brand lg"><i></i>Nexora Labs</span>
      <h1 style="margin-top:20px"><b>Project</b> Title Here</h1>
      <p class="sub">Subtext here Subtext here Subtext here Subtext here<br>Subtext here Subtext here Subtext here</p>
    </div>
    <footer class="footer ruled"><span>Copyright text here</span><span class="page">Page 01</span></footer>
  </section>

  <!-- 3 cover simple -->
  <section class="slide warm" style="background:linear-gradient(135deg,#fff 0%,#fff8f3 50%,#fde8d8 100%)">
    <div class="cover" style="top:96px">
      <span class="brand lg"><i></i>Nexora Labs</span>
      <h1><b>Project</b> Title Here</h1>
      <p class="presenter" style="margin-top:9px">Persentatator Name : <em style="display:inline">Marco Teixeira</em></p>
    </div>
  </section>

  <!-- 4 index -->
  <section class="slide">
    <h2 class="title"><b>Project</b> Title Here</h2>
    <ul class="index">
      <li><span class="num">01</span>Slide Title Here</li><li><span class="num">06</span>Slide Title Here</li>
      <li><span class="num">02</span>Slide Title Here</li><li><span class="num">07</span>Slide Title Here</li>
      <li><span class="num">03</span>Slide Title Here</li><li><span class="num">08</span>Slide Title Here</li>
      <li><span class="num">04</span>Slide Title Here</li><li><span class="num">09</span>Slide Title Here</li>
      <li><span class="num">05</span>Slide Title Here</li><li><span class="num">10</span>Slide Title Here</li>
    </ul>
    <footer class="footer"><span class="who">Persentatator Name : <em>Marco Teixeira</em></span><span class="brand"><i></i>Nexora Labs</span></footer>
  </section>

  <!-- 5 bullets -->
  <section class="slide">
    <h2 class="title"><b>Project</b> Title Here</h2>
    <ul class="bullets">
      <li><svg width="8" height="8" viewBox="0 0 8 8"><rect width="8" height="8" fill="#f26b21"/><path d="M3 2l2 2-2 2" stroke="#fff" fill="none"/></svg>Lorem ipsum dolor sit ipsum Lorem ipsum dolor sit ipsum Lorem ipsum</li>
      <li><svg width="8" height="8" viewBox="0 0 8 8"><rect width="8" height="8" fill="#f26b21"/><path d="M3 2l2 2-2 2" stroke="#fff" fill="none"/></svg>Lorem ipsum dolor sit ipsum Lorem ipsum dolor sit ipsum Lorem ipsum</li>
      <li><svg width="8" height="8" viewBox="0 0 8 8"><rect width="8" height="8" fill="#f26b21"/><path d="M3 2l2 2-2 2" stroke="#fff" fill="none"/></svg>Lorem ipsum dolor sit ipsum Lorem ipsum dolor sit ipsum Lorem ipsum</li>
      <li><svg width="8" height="8" viewBox="0 0 8 8"><rect width="8" height="8" fill="#f26b21"/><path d="M3 2l2 2-2 2" stroke="#fff" fill="none"/></svg>Lorem ipsum dolor sit ipsum Lorem ipsum dolor sit ipsum Lorem ipsum</li>
      <li><svg width="8" height="8" viewBox="0 0 8 8"><rect width="8" height="8" fill="#f26b21"/><path d="M3 2l2 2-2 2" stroke="#fff" fill="none"/></svg>Lorem ipsum dolor sit ipsum Lorem ipsum dolor sit ipsum Lorem ipsum</li>
      <li><svg width="8" height="8" viewBox="0 0 8 8"><rect width="8" height="8" fill="#f26b21"/><path d="M3 2l2 2-2 2" stroke="#fff" fill="none"/></svg>Lorem ipsum dolor sit ipsum Lorem ipsum dolor sit ipsum Lorem ipsum</li>
      <li><svg width="8" height="8" viewBox="0 0 8 8"><rect width="8" height="8" fill="#f26b21"/><path d="M3 2l2 2-2 2" stroke="#fff" fill="none"/></svg>Lorem ipsum dolor sit ipsum Lorem ipsum dolor sit ipsum Lorem ipsum</li>
      <li><svg width="8" height="8" viewBox="0 0 8 8"><rect width="8" height="8" fill="#f26b21"/><path d="M3 2l2 2-2 2" stroke="#fff" fill="none"/></svg>Lorem ipsum dolor sit ipsum Lorem ipsum dolor sit ipsum Lorem ipsum</li>
    </ul>
    <footer class="footer"><span class="who">Persentatator Name : <em>Marco Teixeira</em></span><span class="brand"><i></i>Nexora Labs</span></footer>
  </section>

  <!-- 6 photo band -->
  <section class="slide">
    <h2 class="title"><b>Project</b> Title Here</h2>
    <div class="photo" style="left:0;top:37px;width:287px;height:92px" role="img" aria-label="Photo of a bright open-plan office with white desks and chairs"></div>
    <div style="position:absolute;left:0;top:116px;width:287px;height:13px;background:linear-gradient(90deg,var(--orange),var(--orange-mid));color:#fff;font-size:7px;padding:1px 13px">Slide Title Here</div>
    <div class="cols txt just" style="left:14px;top:137px;width:262px">
      <div><p>Lorem ipsum dolor sit Lorem ipsum dolor sit Lorem ipsum dolor sit Lorem ipsum dolor sit Lorem ipsum dolor sit Lorem ipsum Lorem ipsum</p><p>Lorem ipsum dolor sit Lorem ipsum dolor sit Lorem ipsum dolor sit Lorem ipsum</p></div>
      <div><p>Lorem ipsum dolor sit Lorem ipsum dolor sit Lorem ipsum dolor sit Lorem ipsum dolor sit Lorem ipsum dolor</p><p>Lorem ipsum dolor sit Lorem ipsum dolor sit Lorem ipsum dolor sit Lorem ipsum</p></div>
    </div>
    <footer class="footer"><span class="who">Persentatator Name : <em>Marco Teixeira</em></span><span class="brand"><i></i>Nexora Labs</span></footer>
  </section>

  <!-- 7 about us -->
  <section class="slide">
    <h2 class="title"><b>Project</b> Title Here</h2>
    <div class="photo lilac" style="left:136px;top:33px;width:151px;height:164px" role="img" aria-label="Photo of an office workstation with a white chair"></div>
    <div style="position:absolute;left:0;top:33px;width:136px;height:164px;background:var(--orange);color:#fff;padding:50px 0 0 13px">
      <div style="font-family:'Roboto Condensed',Arial,sans-serif;font-size:13px">ABOUT US</div>
      <p style="font-size:4.6px;line-height:6.4px;font-weight:600">Lorem ipsum dolor sit Lorem ipsum dolor sit<br>Lorem ipsum dolor sit Lorem ipsum dolor sit<br>Lorem ipsum dolor sit Lorem ipsum dolor sit</p>
    </div>
    <footer class="footer"><span class="who">Persentatator Name : <em>Marco Teixeira</em></span><span class="brand"><i></i>Nexora Labs</span></footer>
  </section>

  <!-- 8 two columns -->
  <section class="slide">
    <h2 class="title"><b>Project</b> Title Here</h2>
    <div class="cols txt" style="left:15px;top:52px;width:262px;column-gap:18px">
      <div><h3>Lorem ipsum dolor sit ipsum</h3>
        <p>Lorem ipsum dolor sit ipsum Lorem ipsum dolor sit ipsum Lorem ipsum dolor sit ipsum Lorem ipsum dolor sit ipsum Lorem ipsum dolor sit ipsum Lorem ipsum dolor sit ipsum</p>
        <p style="margin-top:12px">Lorem ipsum dolor sit ipsum Lorem ipsum dolor sit ipsum Lorem ipsum dolor sit ipsum Lorem ipsum dolor sit ipsum Lorem ipsum dolor sit ipsum Lorem ipsum dolor sit ipsum Lorem ipsum dolor sit ipsum</p></div>
      <div><h3>Lorem ipsum dolor sit ipsum</h3>
        <p>Lorem ipsum dolor sit ipsum Lorem ipsum dolor sit ipsum Lorem ipsum dolor sit ipsum Lorem ipsum dolor sit ipsum Lorem ipsum dolor sit ipsum Lorem ipsum dolor sit ipsum</p>
        <p style="margin-top:12px">Lorem ipsum dolor sit ipsum Lorem ipsum dolor sit ipsum Lorem ipsum dolor sit ipsum Lorem ipsum dolor sit ipsum Lorem ipsum dolor sit ipsum Lorem ipsum dolor sit ipsum Lorem ipsum dolor sit ipsum</p></div>
    </div>
    <footer class="footer"><span class="who">Persentatator Name : <em>Marco Teixeira</em></span><span class="brand"><i></i>Nexora Labs</span></footer>
  </section>

  <!-- 9 table -->
  <section class="slide">
    <h2 class="title"><b>Project</b> Title Here</h2>
    <p class="txt" style="position:absolute;left:17px;top:46px;width:262px;color:var(--ink)">Lorem ipsum dolor sit ipsum Lorem ipsum dolor sit ipsum Lorem ipsum Lorem ipsum dolor sit ipsum Lorem ipsum dolor sit ipsum Lorem ipsum</p>
    <table class="table">
      <tr><th>Content Title Here</th><th>Content Title Here</th><th>Content Title Here</th></tr>
      <tr><td>Lorem ipsum dolor Lorem ipsum</td><td>Lorem ipsum dolor Lorem ipsum</td><td>Lorem ipsum dolor Lorem ipsum</td></tr>
      <tr><td>Lorem ipsum dolor Lorem ipsum</td><td>Lorem ipsum dolor Lorem ipsum</td><td>Lorem ipsum dolor Lorem ipsum</td></tr>
      <tr><td>Lorem ipsum dolor Lorem ipsum</td><td>Lorem ipsum dolor Lorem ipsum</td><td>Lorem ipsum dolor Lorem ipsum</td></tr>
      <tr><td>Lorem ipsum dolor Lorem ipsum</td><td>Lorem ipsum dolor Lorem ipsum</td><td>Lorem ipsum dolor Lorem ipsum</td></tr>
    </table>
    <footer class="footer"><span class="who">Persentatator Name : <em>Marco Teixeira</em></span><span class="brand"><i></i>Nexora Labs</span></footer>
  </section>

  <!-- 10 three cards -->
  <section class="slide">
    <h2 class="title"><b>Project</b> Title Here</h2>
    <div class="cards">
      <div><div class="ph">IMAGE HERE</div><div class="lbl">Text Title Here</div><div class="txt just"><p>Lorem ipsum dolor sit Lorem ipsum dolor sit Lorem ipsum dolor sit Lorem ipsum dolor sit Lorem ipsum dolor sit Lorem ipsum dolor sit.</p><p>Lorem ipsum dolor sit Lorem ipsum dolor sit Lorem ipsum</p></div></div>
      <div><div class="ph">IMAGE HERE</div><div class="lbl">Text Title Here</div><div class="txt just"><p>Lorem ipsum dolor sit Lorem ipsum dolor sit Lorem ipsum dolor sit Lorem ipsum dolor sit Lorem ipsum dolor sit Lorem ipsum dolor sit.</p><p>Lorem ipsum dolor sit Lorem ipsum dolor sit Lorem ipsum</p></div></div>
      <div><div class="ph">IMAGE HERE</div><div class="lbl">Text Title Here</div><div class="txt just"><p>Lorem ipsum dolor sit Lorem ipsum dolor sit Lorem ipsum dolor sit Lorem ipsum dolor sit Lorem ipsum dolor sit Lorem ipsum dolor sit.</p><p>Lorem ipsum dolor sit Lorem ipsum dolor sit Lorem ipsum</p></div></div>
    </div>
    <footer class="footer"><span class="who">Persentatator Name : <em>Marco Teixeira</em></span><span class="brand"><i></i>Nexora Labs</span></footer>
  </section>

  <!-- 11 line chart -->
  <section class="slide">
    <h2 class="title" style="border-left:none;top:7px"><b>Project</b> Title Here</h2>
    <svg style="position:absolute;left:0;top:0" width="287" height="215" viewBox="0 0 287 215" font-family="Open Sans, Arial, sans-serif" font-size="4" fill="#666">
      <g stroke="#555" stroke-width=".6">
        <line x1="68" y1="52" x2="68" y2="172"/><line x1="68" y1="172" x2="232" y2="172"/>
      </g>
      <g text-anchor="end">
        <text x="64" y="173">0</text><text x="64" y="157.5">2</text><text x="64" y="142">4</text><text x="64" y="126.5">6</text>
        <text x="64" y="111">8</text><text x="64" y="95.5">10</text><text x="64" y="80">12</text><text x="64" y="64.5">14</text>
      </g>
      <g text-anchor="middle"><text x="94" y="178">2</text><text x="150" y="178">4</text><text x="206" y="178">6</text></g>
      <polyline fill="none" stroke="#c9c9c9" stroke-width="1" points="68,172 80,152 92,140 104,138 118,130 132,122 146,115 160,110 176,104 190,100 204,90 218,76 228,66"/>
      <polyline fill="none" stroke="#777" stroke-width="1" points="68,172 80,148 94,134 108,132 120,122 136,116 150,112 164,106 180,102 194,96 208,84 220,74 228,66"/>
      <polyline fill="none" stroke="#f26b21" stroke-width="1.2" points="68,172 80,150 92,134 104,130 118,120 130,118 144,112 158,104 174,100 188,98 200,92 206,80 218,72 228,64"/>
      <polyline fill="none" stroke="#f26b21" stroke-width="1.2" points="68,172 90,168 110,167 140,168 170,167 190,166 210,168 228,168"/>
    </svg>
    <footer class="footer"><span class="brand"><i></i>Nexora Labs</span><span class="who">Persentatator Name : <em>Marco Teixeira</em></span></footer>
  </section>

  <!-- 12 director -->
  <section class="slide">
    <h2 class="title"><b>Project</b> Title Here</h2>
    <div class="portrait" role="img" aria-label="Portrait placeholder for the technical director">IMAGE HERE DIRECTOR</div>
    <div class="nameband">Marco Teixeira</div>
    <div class="role">Technical Director</div>
    <div class="bio txt just">
      <p>Marco Teixeira has more than 14 years of experience in the IT industry. He has devoted much of his career to becoming a recognized expert in enterprise technologies and software architectures, most specifically in relation to collaboration, databases and messaging servers.</p>
      <p>As Nexora Labs Technical Director, Marco Teixeira oversees development and implementation of strategic IT initiatives and best practices for enterprise clients as well as internally.</p>
      <p>He is particularly adept at applying his deep technical knowledge to large and complex projects and is the senior technical mentor for Northbay's enterprise platform practice. He is involved in all aspects of the Northbay service lifecycle including business development, operations, pre-sales and consulting.</p>
      <p class="contact" style="margin-top:6px">Email : marco.teixeira@nexoralabs.com<br>Fax : (001) 555-0199</p>
    </div>
    <footer class="footer"><span class="who">Persentatator Name : <em>Marco Teixeira</em></span><span class="brand"><i></i>Nexora Labs</span></footer>
  </section>

  <!-- 13 pie -->
  <section class="slide">
    <h2 class="title"><b>Project</b> Title Here</h2>
    <p class="lead" style="position:absolute;left:12px;top:49px">Lorem ipsum dolor sit ipsum</p>
    <div class="txt just" style="position:absolute;left:12px;top:62px;width:132px;color:var(--grey)">
      <p style="margin-bottom:9px">Lorem ipsum dolor sit ipsum Lorem ipsum dolor sit ipsum Lorem ipsum dolor sit ipsum Lorem ipsum dolor sit ipsum Lorem ipsum dolor sit ipsum Lorem ipsum dolor sit ipsum Lorem ipsum dolor sit ipsum</p>
      <p>Lorem ipsum dolor sit ipsum Lorem ipsum dolor sit ipsum Lorem ipsum dolor sit ipsum Lorem ipsum dolor sit ipsum Lorem ipsum dolor sit ipsum Lorem ipsum dolor sit ipsum Lorem ipsum dolor sit ipsum</p>
    </div>
    <svg style="position:absolute;left:160px;top:60px" width="120" height="120" viewBox="-60 -60 120 120" font-family="Open Sans, Arial, sans-serif" font-size="3.6" font-weight="600" fill="#fff" text-anchor="middle">
      <g transform="rotate(-90)" fill="none" stroke-width="54">
        <circle r="27" stroke="#9e9e9e" stroke-dasharray="21.2 148.5"/>
        <circle r="27" stroke="#f26b21" stroke-dasharray="0 21.2 27 148.5"/>
        <circle r="27" stroke="#f6a06b" stroke-dasharray="0 48.2 21 148.5"/>
        <circle r="27" stroke="#f5874a" stroke-dasharray="0 69.2 32 148.5"/>
        <circle r="27" stroke="#4f4f4f" stroke-dasharray="0 101.2 44 148.5"/>
        <circle r="27" stroke="#777" stroke-dasharray="0 145.2 26 148.5"/>
      </g>
      <g stroke="#fff" stroke-width=".8">
        <line x1="0" y1="0" x2="0" y2="-54"/><line x1="0" y1="0" x2="38" y2="-38"/><line x1="0" y1="0" x2="54" y2="6"/>
        <line x1="0" y1="0" x2="30" y2="45"/><line x1="0" y1="0" x2="-28" y2="46"/><line x1="0" y1="0" x2="-52" y2="-14"/><line x1="0" y1="0" x2="-30" y2="-45"/>
      </g>
      <circle r="8" fill="#fff"/><circle r="5" fill="#f26b21"/>
      <text x="12" y="-38">Lorem</text><text x="12" y="-34">ipsum</text>
      <text x="-12" y="-36">Lorem</text><text x="-12" y="-32">ipsum</text>
      <text x="32" y="-4">Lorem ipsum</text><text x="32" y="0">dolor</text>
      <text x="26" y="26">Lorem ipsum</text><text x="26" y="30">dolor</text>
      <text x="-6" y="34">Lorem ipsum dolor</text><text x="-6" y="38">Lorem ipsum dolor</text>
      <text x="-30" y="4">Lorem ipsum dolor</text><text x="-30" y="8">Lorem ipsum dolor</text>
    </svg>
    <footer class="footer"><span class="who">Persentatator Name : <em>Marco Teixeira</em></span><span class="brand"><i></i>Nexora Labs</span></footer>
  </section>

  <!-- 14 bar chart -->
  <section class="slide">
    <h2 class="title" style="border-left:none;top:7px"><b>Project</b> Title Here</h2>
    <p class="txt" style="position:absolute;left:12px;top:40px;color:var(--ink);font-size:5px">Lorem ipsum dolor sit ipsum Lorem ipsum dolor sit ipsum Lorem ipsum Lorem ipsum</p>
    <svg style="position:absolute;left:0;top:0" width="287" height="215" viewBox="0 0 287 215" font-family="Open Sans, Arial, sans-serif" font-size="4" fill="#555">
      <g>
        <text x="12" y="71">Lorem ipsum text here</text><text x="12" y="86">Lorem ipsum text here</text>
        <text x="12" y="101">Lorem ipsum text here</text><text x="12" y="119">Lorem ipsum text here</text>
        <text x="12" y="134">Lorem ipsum text here</text><text x="12" y="152">Lorem ipsum text here</text>
        <text x="12" y="167">Lorem ipsum text here</text>
      </g>
      <line x1="62" y1="165" x2="246" y2="165" stroke="#bbb" stroke-width=".6"/>
      <rect x="62" y="131" width="11" height="34" fill="#9a9a9a"/>
      <rect x="77" y="104" width="15" height="61" fill="#f26b21"/>
      <rect x="94" y="111" width="14" height="54" fill="#f08a5a"/>
      <rect x="112" y="136" width="13" height="29" fill="#f7b55a"/>
      <rect x="132" y="156" width="14" height="9" fill="#f26b21"/>
      <rect x="152" y="161" width="14" height="4" fill="#9a9a9a"/>
      <rect x="170" y="69" width="14" height="96" fill="#f26b21"/>
      <rect x="189" y="156" width="14" height="9" fill="#f26b21"/>
      <rect x="207" y="160" width="14" height="5" fill="#f7b55a"/>
      <text x="60" y="175">Lorem ipsum text here</text><text x="129" y="175">Lorem ipsum text here</text><text x="202" y="175">Lorem ipsum text here</text>
    </svg>
    <footer class="footer"><span class="brand"><i></i>Nexora Labs</span><span class="who">Persentatator Name : <em>Marco Teixeira</em></span></footer>
  </section>

  <!-- 15 agenda -->
  <section class="slide">
    <h2 class="title"><b>Project</b> Title Here</h2>
    <div class="agenda-h">AGENDA TITLE HERE</div>
    <div class="agenda">
      <div class="row"><div class="chev"><svg width="40" height="30" viewBox="0 0 40 30"><path d="M0 0 20 6 40 0V22L20 30 0 22Z" fill="#f26b21"/></svg><span>Text Here</span></div><div class="box">› Lorem ipsum dolor sit ipsum Lorem ipsum dolor sit ipsum Lorem ipsum<br>› Lorem ipsum dolor sit ipsum Lorem ipsum dolor sit ipsum Lorem ipsum</div></div>
      <div class="row"><div class="chev"><svg width="40" height="30" viewBox="0 0 40 30"><path d="M0 0 20 6 40 0V22L20 30 0 22Z" fill="#f26b21"/></svg><span>Text Here</span></div><div class="box">› Lorem ipsum dolor sit ipsum Lorem ipsum dolor sit ipsum Lorem ipsum<br>› Lorem ipsum dolor sit ipsum Lorem ipsum dolor sit ipsum Lorem ipsum</div></div>
      <div class="row"><div class="chev"><svg width="40" height="30" viewBox="0 0 40 30"><path d="M0 0 20 6 40 0V22L20 30 0 22Z" fill="#f26b21"/></svg><span>Text Here</span></div><div class="box">› Lorem ipsum dolor sit ipsum Lorem ipsum dolor sit ipsum Lorem ipsum<br>› Lorem ipsum dolor sit ipsum Lorem ipsum dolor sit ipsum Lorem ipsum</div></div>
      <div class="row"><div class="chev"><svg width="40" height="30" viewBox="0 0 40 30"><path d="M0 0 20 6 40 0V22L20 30 0 22Z" fill="#f26b21"/></svg><span>Text Here</span></div><div class="box">› Lorem ipsum dolor sit ipsum Lorem ipsum dolor sit ipsum Lorem ipsum<br>› Lorem ipsum dolor sit ipsum Lorem ipsum dolor sit ipsum Lorem ipsum</div></div>
    </div>
    <footer class="footer"><span class="who">Persentatator Name : <em>Marco Teixeira</em></span><span class="brand"><i></i>Nexora Labs</span></footer>
  </section>

  <!-- 16 closing -->
  <section class="slide warm" style="background:linear-gradient(135deg,#fff 0%,#fff6ef 40%,#fde6d4 100%)">
    <div class="closing-brand"><span class="brand" style="font-size:15px;gap:4px"><i style="width:9px;height:9px"></i>Nexora Labs</span></div>
    <p class="closing-presenter">Persentatator Name : <em>Marco Teixeira</em></p>
    <div class="contact-card">
      <h2>Project Title Here</h2>
      <p class="txt">Contact Details line here Contact Details line here, Contact Details line here</p>
      <ul>
        <li><svg width="7" height="7" viewBox="0 0 10 10"><circle cx="5" cy="5" r="5" fill="#f26b21"/><path d="M3.3 2.5c.3 2 1.8 3.8 3.9 4.3l.5-.9-1-.6-.5.5c-.9-.4-1.6-1.2-1.9-2.1l.5-.5-.6-1z" fill="#fff"/></svg>01 5550 123456</li>
        <li><svg width="7" height="7" viewBox="0 0 10 10"><circle cx="5" cy="5" r="5" fill="#f26b21"/><rect x="2.5" y="3.2" width="5" height="3.6" fill="none" stroke="#fff" stroke-width=".7"/><path d="M2.5 3.2 5 5.2 7.5 3.2" fill="none" stroke="#fff" stroke-width=".7"/></svg>info@nexoralabs.com</li>
        <li><svg width="7" height="7" viewBox="0 0 10 10"><circle cx="5" cy="5" r="5" fill="#f26b21"/><circle cx="5" cy="5" r="2.6" fill="none" stroke="#fff" stroke-width=".7"/><line x1="2.4" y1="5" x2="7.6" y2="5" stroke="#fff" stroke-width=".6"/></svg>www.nexoralabs.com</li>
      </ul>
    </div>
  </section>

</main>
</body>
</html>
```